Road Construction Company needs business cards

We would like a new business card designed for our business.

We're a road construction company based in Qld, Australia.

Can the business card please have the following information on it.

Name: Warren Halbeck
Position: General Manager
Phone: 0472 915 348
Email: Warren.halbeck@tovrin.com.au
Address: 87 Marrow Ave, Pendlebay, QLD, 4023
Website: www.tovrin.com.au

Visually we'd like the card to be professional and simple.

Attached is our logo.

Our website is www.tovrin.com.au

Target Market(s)

Men aged 25-60

Contact Information for Business Card

As listed in project description

Font styles to use
Serif

Requirements
Must have
• Large logo on back of card

```html
<!DOCTYPE html>
<html lang="en">
<head>
<meta charset="utf-8">
<title>Tovrin Business Card</title>
<link rel="stylesheet" href="https://fonts.googleapis.com/css2?family=Nunito+Sans:wght@400;700;800&display=swap">
<style>
  :root {
    --backdrop: #e4e4e4;
    --brand-blue: #0c4a96;
    --brand-blue-deep: #083c85;
    --brand-blue-light: #1668b3;
    --card-white: #f1f1f1;
    --text-grey: #5a5d63;
    --text-white: #ffffff;
  }
  * { box-sizing: border-box; margin: 0; padding: 0; }
  html, body { width: 1200px; height: 1200px; overflow: hidden; }
  body {
    background: var(--backdrop);
    font-family: "Nunito Sans", sans-serif;
    position: relative;
  }
  .card {
    position: absolute;
    left: 233px;
    width: 732px;
    height: 418px;
    overflow: hidden;
  }
  .card-front { top: 160px; }
  .card-back { top: 632px; background: linear-gradient(120deg, #e9e9e9, var(--card-white) 60%, #f5f5f5); }

  .front-field {
    position: absolute; inset: 0;
    background: linear-gradient(135deg, var(--brand-blue-deep), var(--brand-blue) 50%, var(--brand-blue-light));
  }
  .front-wordmark {
    position: absolute; left: 0; right: 0; top: 174px;
    text-align: center;
    color: var(--text-white);
    font-weight: 800;
    font-size: 54px;
    letter-spacing: 2px;
    line-height: 1;
  }

  .holder { position: absolute; left: 65px; top: 48px; }
  .holder-name { color: var(--brand-blue); font-weight: 800; font-size: 32px; line-height: 1.1; }
  .holder-title { color: var(--text-grey); font-size: 19px; margin-top: 4px; }

  .back-wordmark {
    position: absolute; right: 65px; top: 52px;
    color: var(--brand-blue);
    font-weight: 800;
    font-size: 40px;
    letter-spacing: 2px;
    line-height: 1;
  }

  .contact { position: absolute; display: flex; align-items: center; gap: 9px;
    color: var(--text-grey); font-size: 19.5px; line-height: 1; }
  .contact svg { width: 17px; height: 17px; fill: var(--brand-blue); flex: none; }
  .contact-phone { left: 64px; top: 274px; }
  .contact-email { left: 64px; top: 302px; }
  .contact-web { left: 461px; top: 302px; }

  .address-band {
    position: absolute; left: 0; right: 0; bottom: 0; height: 56px;
    background: var(--brand-blue-deep);
    color: var(--text-white);
    font-size: 19.5px;
    display: flex; align-items: center; justify-content: center;
  }
</style>
</head>
<body>
  <section class="card card-front">
    <div class="front-field" role="img" aria-label="Embossed pattern of upward chevrons on a blue gradient"></div>
    <div class="front-wordmark">TOVRIN</div>
  </section>

  <section class="card card-back">
    <div class="holder">
      <p class="holder-name">Warren Halbeck</p>
      <p class="holder-title">General Manager</p>
    </div>
    <div class="back-wordmark">TOVRIN</div>

    <p class="contact contact-phone">
      <svg viewBox="0 0 24 24" aria-hidden="true"><path d="M6.6 10.8a15.1 15.1 0 0 0 6.6 6.6l2.2-2.2a1 1 0 0 1 1-.25 11.4 11.4 0 0 0 3.6.57 1 1 0 0 1 1 1V20a1 1 0 0 1-1 1A17 17 0 0 1 3 4a1 1 0 0 1 1-1h3.5a1 1 0 0 1 1 1c0 1.25.2 2.45.57 3.6a1 1 0 0 1-.25 1z"/></svg>
      0472 915 348
    </p>
    <p class="contact contact-email">
      <svg viewBox="0 0 24 24" aria-hidden="true"><path d="M2 5h20v14H2z M3.5 6.5 12 12.5l8.5-6z" fill-rule="evenodd"/><path d="M2 5l10 7 10-7v-0H2z" fill="#fff" opacity=".0"/></svg>
      Warren.halbeck@tovrin.com.au
    </p>
    <p class="contact contact-web">
      <svg viewBox="0 0 24 24" aria-hidden="true"><path d="M12 2a10 10 0 1 0 0 20 10 10 0 0 0 0-20zm-1 2.1V11H7.1c.2-3 1.6-5.6 3.9-6.9zm2 0c2.3 1.3 3.7 3.9 3.9 6.9H13zM4.1 13H5.1c.1 2.3.8 4.4 2 5.9A8 8 0 0 1 4.1 13zm0-2a8 8 0 0 1 3-5.9c-1.2 1.5-1.9 3.6-2 5.9zm3 2H11v6.9c-2.3-1.3-3.7-3.9-3.9-6.9zm5.9 0h3.9c-.2 3-1.6 5.6-3.9 6.9zm5.9 0h1A8 8 0 0 1 16.9 18.9c1.2-1.5 1.9-3.6 2-5.9zm0-2c-.1-2.3-.8-4.4-2-5.9a8 8 0 0 1 3 5.9z"/></svg>
      www.tovrin.com.au
    </p>

    <div class="address-band">87 Marrow Ave, Pendlebay, QLD, 4023</div>
  </section>
</body>
</html>
```